TA BRAMLEY BUSINESS CARD DESIGN PROJECT

We need to utilize our logo that was expertly created on PixelHarbor and now need to match this with a business card design.

```html
<!DOCTYPE html>
<html lang="en">
<head>
<meta charset="UTF-8">
<title>TA Bramley Business Card</title>
<link href="https://fonts.googleapis.com/css2?family=Montserrat:wght@400;500;700&display=swap" rel="stylesheet">
<style>
  :root {
    --page-bg: #2a2a2c;
    --card-black: #171717;
    --brand-blue: #0d57b0;
    --brand-blue-deep: #0a4a98;
    --text-light: #e8e8e8;
  }
  * { margin: 0; padding: 0; box-sizing: border-box; }
  html, body {
    width: 1200px; height: 780px; overflow: hidden;
    background: var(--page-bg);
    font-family: "Montserrat", sans-serif;
  }
  .stage { position: relative; width: 1200px; height: 780px; }
  .card {
    position: absolute; top: 240px;
    width: 520px; height: 300px;
    border-radius: 26px; overflow: hidden;
  }
  .card-front { left: 50px; background: var(--card-black); }
  .card-back { left: 630px; background: var(--brand-blue); display: flex; align-items: center; justify-content: center; }
  .front-swoosh { position: absolute; inset: 0; }
  .brand-lockup {
    position: absolute; left: 40px; top: 108px; width: 200px;
    display: flex; align-items: center; gap: 10px;
  }
  .brand-square { width: 14px; height: 14px; background: var(--brand-blue); flex: none; }
  .brand-name {
    color: var(--brand-blue); font-weight: 700; font-size: 24px; letter-spacing: 3px; white-space: nowrap;
  }
  .divider {
    position: absolute; left: 262px; top: 60px; width: 1px; height: 150px;
    background: var(--brand-blue);
  }
  .contact-block { position: absolute; left: 284px; top: 58px; color: var(--text-light); }
  .person-name { color: var(--brand-blue); font-weight: 700; font-size: 19px; letter-spacing: 0.5px; }
  .person-title { font-size: 13px; margin: 2px 0 10px; }
  .contact-list { list-style: none; font-size: 12.5px; line-height: 20px; }
  .contact-list li { display: flex; align-items: center; gap: 8px; }
  .contact-list svg { width: 11px; height: 11px; fill: var(--brand-blue); flex: none; }
  .address { font-size: 12.5px; line-height: 19px; margin-top: 4px; }
  .back-name {
    color: var(--brand-blue-deep); font-weight: 700; font-size: 46px; letter-spacing: 8px;
  }
</style>
</head>
<body>
<main class="stage">
  <section class="card card-front">
    <svg class="front-swoosh" viewBox="0 0 520 300" preserveAspectRatio="none">
      <path d="M0 250 C150 235 300 250 520 300 L0 300 Z" fill="var(--brand-blue)"/>
      <path d="M0 238 C160 222 320 240 520 292" fill="none" stroke="var(--brand-blue)" stroke-width="1.5"/>
    </svg>
    <div class="brand-lockup">
      <span class="brand-square"></span>
      <span class="brand-name">TA BRAMLEY</span>
    </div>
    <div class="divider"></div>
    <div class="contact-block">
      <p class="person-name">MARCUS HALE</p>
      <p class="person-title">Managing Director</p>
      <ul class="contact-list">
        <li><svg viewBox="0 0 10 10"><path d="M2 0h2l1 3-1.5 1a6 6 0 0 0 2.5 2.5L7 5l3 1v2c0 1-1 2-2 2A8 8 0 0 1 0 2c0-1 1-2 2-2z"/></svg>123 456 789</li>
        <li><svg viewBox="0 0 10 10"><rect x="1" y="0" width="8" height="10" rx="1.5"/></svg>123 456 789</li>
        <li><svg viewBox="0 0 10 10"><path d="M0 2h10v6H0z M0 2l5 3 5-3" /></svg>info@yourmail.com</li>
        <li><svg viewBox="0 0 10 10"><circle cx="5" cy="5" r="5"/></svg>www.yourwebsite.com</li>
      </ul>
      <p class="address">Your address, City<br>State, Zip 1234</p>
    </div>
  </section>
  <section class="card card-back">
    <span class="back-name">TA BRAMLEY</span>
  </section>
</main>
</body>
</html>
```